Copper Ridge Inquiries Letterhead

I would like to design a letterhead for a private investigation company. Our primary clients will be law firms. The business card is included below

```html
<!DOCTYPE html>
<html lang="en">
<head>
<meta charset="utf-8">
<title>Copper Ridge Inquiries Letterhead</title>
<link rel="stylesheet" href="https://fonts.googleapis.com/css2?family=Lato:wght@400;700&family=Montserrat:wght@400;700&display=swap">
<style>
  :root {
    --navy: #1b3461;
    --orange: #f05f33;
    --pin: #f59a23;
    --alert: #e8342c;
    --ink: #1c1c1c;
    --muted: #3a3a3a;
    --backdrop: #e6e6e6;
    --paper: #ffffff;
  }
  html, body {
    margin: 0;
    width: 1200px;
    height: 1079px;
    overflow: hidden;
    background: var(--backdrop);
  }
  .letterhead {
    position: absolute;
    left: 240px;
    top: 30px;
    width: 720px;
    height: 1018px;
    background: var(--paper);
    box-shadow: 0 2px 10px rgba(0,0,0,0.12);
    overflow: hidden;
    font-family: "Lato", sans-serif;
    color: var(--ink);
  }
  .header-wave {
    position: absolute;
    left: 0;
    top: 0;
    width: 720px;
    height: 194px;
  }
  .brand {
    position: absolute;
    left: 420px;
    top: 40px;
    width: 220px;
    display: flex;
    flex-direction: column;
    align-items: center;
    gap: 10px;
    font-family: "Montserrat", sans-serif;
  }
  .brand-dot {
    width: 40px;
    height: 40px;
    border-radius: 50%;
    background: var(--orange);
  }
  .brand-name {
    color: #ffffff;
    font-weight: 700;
    font-size: 15px;
    letter-spacing: 0.5px;
    white-space: nowrap;
  }
  .contact {
    position: absolute;
    left: 36px;
    top: 192px;
    font-family: "Montserrat", sans-serif;
    font-size: 12.5px;
    color: var(--muted);
    line-height: 18px;
  }
  .contact-line {
    display: flex;
    align-items: center;
    gap: 7px;
  }
  .contact-line svg { width: 10px; height: 10px; }
  .license { margin-top: 7px; }
  .letter-date {
    position: absolute;
    left: 36px;
    top: 321px;
    font-size: 15px;
  }
  .recipient, .recipient-company {
    position: absolute;
    left: 36px;
    font-size: 14px;
    line-height: 17px;
  }
  .recipient { top: 356px; }
  .recipient-company { top: 406px; }
  .salutation {
    position: absolute;
    left: 36px;
    top: 476px;
    margin: 0;
    font-size: 18px;
    font-weight: 700;
  }
  .letter-body {
    position: absolute;
    left: 36px;
    top: 517px;
    width: 648px;
    font-size: 13.4px;
    line-height: 15.8px;
    text-align: justify;
  }
  .letter-body p { margin: 0 0 15.8px; }
  .closing {
    position: absolute;
    left: 36px;
    top: 808px;
    font-size: 14px;
  }
  .signature {
    position: absolute;
    left: 36px;
    top: 874px;
    width: 200px;
    height: 30px;
    background: linear-gradient(90deg, #e9e9e9, #f3f3f3);
  }
  .footer-band {
    position: absolute;
    left: 0;
    bottom: 0;
    width: 720px;
    height: 24px;
  }
</style>
</head>
<body>
  <main class="letterhead">
    <svg class="header-wave" viewBox="0 0 1004 270" preserveAspectRatio="none" aria-hidden="true">
      <path fill="var(--orange)" d="M250,132 C470,165 610,250 780,257 C880,260 950,222 983,170 C935,215 865,243 780,243 C600,238 430,160 250,132 Z"/>
      <path fill="var(--navy)" d="M0,0 H1004 V122 C930,205 860,232 770,232 C600,232 420,170 300,128 C200,100 100,92 0,122 Z"/>
    </svg>

    <div class="brand">
      <span class="brand-dot"></span>
      <span class="brand-name">COPPER RIDGE INQUIRIES</span>
    </div>

    <div class="contact">
      <div class="contact-line">
        <svg viewBox="0 0 10 10" aria-hidden="true"><path fill="var(--pin)" d="M5 0a3.6 3.6 0 0 0-3.6 3.6C1.4 6.3 5 10 5 10s3.6-3.7 3.6-6.4A3.6 3.6 0 0 0 5 0zm0 5a1.4 1.4 0 1 1 0-2.8A1.4 1.4 0 0 1 5 5z"/></svg>
        <span>FLAGSTAFF, AZ</span>
      </div>
      <div class="contact-line">
        <svg viewBox="0 0 10 10" aria-hidden="true"><path fill="var(--alert)" d="M0 4.2C1.5 2.4 3.2 2 5 2s3.5.4 5 2.2L8.6 5.6 7 4.6V3.8C6.3 3.5 5.6 3.4 5 3.4s-1.3.1-2 .4v.8L1.4 5.6zM2 6h6v3H2z"/></svg>
        <span>928.555.0142</span>
      </div>
      <div class="contact-line">
        <svg viewBox="0 0 10 10" aria-hidden="true"><rect x="1" y="2" width="8" height="6" rx="1" fill="none" stroke="var(--alert)" stroke-width="1.3"/><path d="M1.5 2.8 5 5.5l3.5-2.7" fill="none" stroke="var(--alert)" stroke-width="1.1"/></svg>
        <span>DANA@COPPERRIDGEINQUIRIES.COM</span>
      </div>
      <div class="license">LICENSE NO. 02749316</div>
    </div>

    <div class="letter-date">January-03-2020</div>

    <div class="recipient">Mr, John Doe<br>President</div>

    <div class="recipient-company">Link Corpporation<br>123 Street Name, Suite# 10<br>City, State, 120023</div>

    <h1 class="salutation">Dear Mr, John</h1>

    <div class="letter-body">
      <p>Lorem ipsum dolor sit amet, consectetur adipiscing elit, sed do eiusmod tempor incididunt ut labore et dolore magna aliqua. Ut enim ad minim veniam, quis nostrud exercitation ullamco laboris nisi ut aliquip ex ea commodo consequat. Duis aute irure dolor in reprehenderit in voluptate velit esse cillum dolore eu fugiat nulla pariatur.</p>
      <p>Lorem ipsum dolor sit amet, consectetur adipiscing elit, sed do eiusmod tempor incididunt ut labore et dolore magna aliqua. Ut enim ad minim veniam, quis nostrud exercitation ullamco laboris nisi ut aliquip ex ea commodo consequat. Duis aute irure dolor in reprehenderit in voluptate velit esse cillum dolore eu fugiat nulla pariatur.</p>
      <p>Lorem ipsum dolor sit amet, consectetur adipiscing elit, sed do eiusmod tempor incididunt ut labore et dolore magna aliqua. Ut enim ad minim veniam, quis nostrud exercitation ullamco laboris nisi ut aliquip ex ea commodo consequat.</p>
      <p>Excepteur sint occaecat cupidatat non proident, sunt in culpa qui officia deserunt mollit anim id est laborum. re et dolore magnam aliquam quaerat voluptatem.</p>
    </div>

    <div class="closing">Regards</div>

    <div class="signature" role="img" aria-label="Handwritten signature of the sender"></div>

    <svg class="footer-band" viewBox="0 0 1004 33" preserveAspectRatio="none" aria-hidden="true">
      <path fill="var(--navy)" d="M0,0 H498 L448,33 H0 Z"/>
      <path fill="var(--orange)" d="M518,0 H1004 V33 H468 Z"/>
    </svg>
  </main>
</body>
</html>
```